Website Design - TallyPorchHelpers.net

PLEASE CHECK WORD DOCUMENT ATTACHED FOR WEBSITE FLOW.

Target Market(s)

REAL ESTATE AGENTS ARE THE TARGET MARKET

Industry/Entity Type

Real Estate

Coding

Coded - Design and coding required

Number of Pages Required

4 page

Colors

Designer to choose colors to be used in the design.

Requirements
Must have
• WE LIKE RED LOGO ATTACHED
Nice to have
• PLEASE CHECK WORD DOCUMENT ATTACHED FOR WEBSITE FLOW.
Should not have

```html
<!DOCTYPE html>
<html lang="en">
<head>
<meta charset="utf-8">
<title>Tally Porch Helpers</title>
<link href="https://fonts.googleapis.com/css2?family=Lato:wght@400;700;900&family=Montserrat:wght@600;700&display=swap" rel="stylesheet">
<style>
:root{
  --red:#e30a1f;
  --navy:#262180;
  --ink:#1d1d1d;
  --muted:#555;
  --line:#d8d8d8;
  --white:#fff;
  --page:#f6f6f6;
}
*{box-sizing:border-box;margin:0;padding:0}
html,body{width:1200px;height:2616px;overflow:hidden}
body{position:relative;background:var(--white);font-family:"Lato",sans-serif;color:var(--ink)}
.abs{position:absolute}

/* header */
.site-header{left:0;top:0;width:1200px;height:118px;background:var(--white);border-top:4px solid var(--red)}
.brand{left:98px;top:36px;display:flex;align-items:center;gap:10px}
.brand-mark{width:30px;height:30px;background:var(--navy)}
.brand-name{font-weight:900;font-size:22px;line-height:22px;color:var(--navy);text-transform:uppercase;width:170px}
.main-nav{left:462px;top:50px;display:flex;gap:30px;font-weight:700;font-size:14px;color:var(--ink)}
.phone-btn{left:917px;top:38px;width:183px;height:42px;border-radius:21px;background:var(--red);color:var(--white);font-weight:700;font-size:15px;display:flex;align-items:center;padding-left:10px;gap:12px}
.phone-btn .dot{width:28px;height:28px;border-radius:50%;background:var(--white);display:flex;align-items:center;justify-content:center}

/* hero */
.hero{left:0;top:118px;width:1200px;height:510px;background:linear-gradient(180deg,#8a8f76 0%,#6f7652 35%,#4f7a2a 62%,#3f6e1f 100%)}
.hero-title{left:535px;top:262px;font-family:"Montserrat",sans-serif;font-weight:700;color:var(--white);letter-spacing:6px;line-height:62px}
.hero-title .l1{font-size:64px;display:block}
.hero-title .l2{font-size:52px;display:block}
.hero-text{left:535px;top:414px;width:580px;color:var(--white);font-size:19px;line-height:30px}

/* middle backdrop */
.mid-backdrop{left:0;top:628px;width:1200px;height:1667px;background:linear-gradient(160deg,#fafafa 0%,#f0f0f0 45%,#f7f7f7 100%)}

.section-title{left:0;width:1200px;text-align:center;font-weight:700;color:var(--ink)}
.choose-title{top:716px;font-size:34px;line-height:52px}
.role-circle{width:140px;height:140px;border-radius:50%;background:var(--white);border:2px solid #e4e4e4;display:flex;align-items:center;justify-content:center}
.role-circle .art{width:78px;height:78px;border-radius:50%;background:linear-gradient(180deg,#d6d5ec,#b9b7de)}
.role-label{width:320px;text-align:center;font-weight:700;font-size:16px;top:1016px}
.role-active{left:434px;top:1010px;width:314px;height:38px;border-radius:19px;background:var(--red);color:var(--white);font-weight:700;font-size:16px;display:flex;align-items:center;justify-content:center}
.divider{left:98px;top:1165px;width:1004px;height:1px;background:var(--line)}
.packages-title{top:1252px;font-size:34px}

/* plans */
.plan{background:var(--white);box-shadow:0 2px 10px rgba(0,0,0,.12);border-radius:4px;text-align:center}
.plan-name{font-weight:700;font-size:30px;padding-top:12px;height:60px}
.plan-band{height:46px;background:var(--navy);color:var(--white);font-weight:700;font-size:22px;letter-spacing:2px;display:flex;align-items:center;justify-content:center}
.plan-list{list-style:none;text-align:left;padding:30px 26px 0 28px}
.plan-list li{display:flex;gap:12px;font-size:13px;line-height:21px;color:var(--muted);margin-bottom:16px}
.plan-list li svg{flex:none;margin-top:3px}
.buy{display:inline-flex;align-items:center;justify-content:center;width:124px;height:34px;border-radius:17px;border:2px solid var(--navy);color:var(--navy);font-weight:700;font-size:14px}
.plan-featured{border-top-left-radius:6px;border-top-right-radius:6px;border-bottom:3px solid var(--navy)}
.plan-featured .plan-name{background:var(--navy);color:var(--white);border-radius:6px 6px 0 0}
.plan-featured .plan-band{background:var(--red)}
.plan-featured .buy{background:var(--red);border-color:var(--red);color:var(--white)}
.arrow{top:1580px}

/* services */
.addon-lead{top:1895px;font-weight:400;font-size:23px}
.addon-title{top:1935px;font-size:34px}
.service{top:2030px;height:105px;background:var(--white);box-shadow:0 2px 10px rgba(0,0,0,.1);display:flex;align-items:center;justify-content:center;gap:16px;font-weight:700;font-size:26px;color:var(--ink)}
.service-active{background:var(--red);color:var(--white)}
.service-active .sq{width:26px;height:26px;background:var(--white)}
.service-note{left:615px;top:2135px;width:225px;height:88px;background:var(--white);font-size:13px;line-height:21px;color:var(--muted);text-align:center;padding-top:28px;box-shadow:0 4px 10px rgba(0,0,0,.08)}

/* footer */
.site-footer{left:0;top:2295px;width:1200px;height:321px;background:var(--navy);color:var(--white)}
.footer-brand{left:98px;top:2375px;display:flex;align-items:center;gap:14px}
.footer-brand .sq{width:40px;height:40px;background:var(--white)}
.footer-brand .name{font-weight:900;font-size:32px;line-height:32px;width:200px;text-transform:uppercase}
.footer-head{font-weight:700;font-size:16px;top:2372px}
.socials{left:466px;top:2418px;display:flex;gap:12px}
.socials span{width:44px;height:44px;border-radius:50%;background:var(--white);border:3px solid var(--red)}
.socials span.on{background:var(--red);border-color:var(--white)}
.email-field{left:800px;top:2413px;width:300px;height:40px;border:1px solid var(--white);display:flex;align-items:center;justify-content:space-between;padding:0 14px;font-size:14px}
.subscribe{left:800px;top:2466px;width:125px;height:38px;border-radius:19px;background:var(--red);font-weight:700;font-size:14px;display:flex;align-items:center;justify-content:center}
.footer-rule{left:98px;top:2533px;width:1004px;height:1px;background:rgba(255,255,255,.35)}
.copyright{left:0;top:2570px;width:1200px;text-align:center;font-weight:700;font-size:14px}
</style>
</head>
<body>

<header class="abs site-header">
  <div class="abs brand"><span class="brand-mark"></span><span class="brand-name">Tally Porch Helpers</span></div>
  <nav class="abs main-nav"><span>HOW IT WORKS</span><span>SERVICE</span><span>PRICING</span><span>ABOUT US</span><span>FAQ</span></nav>
  <div class="abs phone-btn"><span class="dot"><svg width="16" height="16" viewBox="0 0 24 24"><path fill="#e30a1f" d="M6.6 10.8a15.1 15.1 0 0 0 6.6 6.6l2.2-2.2c.3-.3.7-.4 1-.2 1.1.4 2.3.6 3.6.6.6 0 1 .4 1 1V20c0 .6-.4 1-1 1A17 17 0 0 1 3 4c0-.6.4-1 1-1h3.5c.6 0 1 .4 1 1 0 1.3.2 2.5.6 3.6.1.3 0 .7-.2 1z"/></svg></span>(+1) 555 014 2290</div>
</header>

<section class="abs hero" role="img" aria-label="Photo of a red open house sign on a front lawn before a large home"></section>
<h1 class="abs hero-title"><span class="l1">TALLY PORCH</span><span class="l2">HELPERS</span></h1>
<p class="abs hero-text">Helping agents save time and money. We place signs and boost foot traffic to your open houses using proven marketing techniques.</p>

<div class="abs mid-backdrop" role="img" aria-label="Faint photo of a desk with paperwork and a pen"></div>

<h2 class="abs section-title choose-title">CHOOSE THE OPTION BELOW THAT<br>BEST DESCRIBES YOU</h2>

<div class="abs role-circle" style="left:145px;top:846px"><div class="art" role="img" aria-label="Icon of an agent"></div></div>
<div class="abs role-circle" style="left:521px;top:846px"><div class="art" role="img" aria-label="Icon of a team of agents"></div></div>
<div class="abs role-circle" style="left:897px;top:846px"><div class="art" role="img" aria-label="Icon of a house location pin on a map"></div></div>
<p class="abs role-label" style="left:55px">I'M A FULL ON BROKERAGE</p>
<div class="abs role-active">I'M AN IND. BROKER WITH A TEAM</div>
<p class="abs role-label" style="left:805px">I NEED SIGN PLACEMENT ASAP</p>

<div class="abs divider"></div>
<h2 class="abs section-title packages-title">OUR PACKAGES</h2>

<svg class="abs arrow" style="left:68px" width="20" height="30" viewBox="0 0 20 30"><path d="M16 3 4 15l12 12" fill="none" stroke="#555" stroke-width="3"/></svg>
<svg class="abs arrow" style="left:1110px" width="20" height="30" viewBox="0 0 20 30"><path d="M4 3l12 12L4 27" fill="none" stroke="#555" stroke-width="3"/></svg>

<article class="abs plan" style="left:115px;top:1402px;width:313px;height:386px">
  <h3 class="plan-name">Plan 1</h3>
  <div class="plan-band">05 SIGNS</div>
  <ul class="plan-list">
    <li><svg width="14" height="12" viewBox="0 0 14 12"><path d="M1 6h9M7 2l4 4-4 4" fill="none" stroke="#e30a1f" stroke-width="2"/></svg>Place signs strategically in best areas according to where the open house is located</li>
    <li><svg width="14" height="12" viewBox="0 0 14 12"><path d="M1 6h9M7 2l4 4-4 4" fill="none" stroke="#e30a1f" stroke-width="2"/></svg>Pick Up the signs after the open house</li>
    <li><svg width="14" height="12" viewBox="0 0 14 12"><path d="M1 6h9M7 2l4 4-4 4" fill="none" stroke="#e30a1f" stroke-width="2"/></svg>Store custom signs for you if needed</li>
  </ul>
  <span class="buy">BUY NOW</span>
</article>

<article class="abs plan plan-featured" style="left:445px;top:1352px;width:312px;height:456px">
  <h3 class="plan-name">Plan 2</h3>
  <div class="plan-band">10 SIGNS</div>
  <ul class="plan-list" style="padding-top:26px">
    <li><svg width="14" height="12" viewBox="0 0 14 12"><path d="M1 6h9M7 2l4 4-4 4" fill="none" stroke="#262180" stroke-width="2"/></svg>Place signs strategically in best areas according to where the open house is located</li>
    <li><svg width="14" height="12" viewBox="0 0 14 12"><path d="M1 6h9M7 2l4 4-4 4" fill="none" stroke="#262180" stroke-width="2"/></svg>Pick Up the signs after the open house</li>
    <li><svg width="14" height="12" viewBox="0 0 14 12"><path d="M1 6h9M7 2l4 4-4 4" fill="none" stroke="#262180" stroke-width="2"/></svg>Store custom signs for you if needed</li>
    <li><svg width="14" height="12" viewBox="0 0 14 12"><path d="M1 6h9M7 2l4 4-4 4" fill="none" stroke="#262180" stroke-width="2"/></svg>Lorem ipsum dolor sit amet, consectetur adipiscing elit,</li>
  </ul>
  <span class="buy">BUY NOW</span>
</article>

<article class="abs plan" style="left:772px;top:1402px;width:313px;height:386px">
  <h3 class="plan-name">Plan 3</h3>
  <div class="plan-band">15 SIGNS</div>
  <ul class="plan-list">
    <li><svg width="14" height="12" viewBox="0 0 14 12"><path d="M1 6h9M7 2l4 4-4 4" fill="none" stroke="#e30a1f" stroke-width="2"/></svg>Place signs strategically in best areas according to where the open house is located</li>
    <li><svg width="14" height="12" viewBox="0 0 14 12"><path d="M1 6h9M7 2l4 4-4 4" fill="none" stroke="#e30a1f" stroke-width="2"/></svg>Pick Up the signs after the open house</li>
    <li><svg width="14" height="12" viewBox="0 0 14 12"><path d="M1 6h9M7 2l4 4-4 4" fill="none" stroke="#e30a1f" stroke-width="2"/></svg>Store custom signs for you if needed</li>
  </ul>
  <span class="buy">BUY NOW</span>
</article>

<p class="abs section-title addon-lead">Ability To Add On Marketing Services-Sign Up For A Subscription And Get These</p>
<h2 class="abs section-title addon-title">MARKETING SERVICES FOR FREE</h2>

<div class="abs service" style="left:100px;width:175px">
  <svg width="54" height="40" viewBox="0 0 54 40"><ellipse cx="27" cy="18" rx="24" ry="15" fill="#262180"/><path d="M12 28l-4 10 12-7z" fill="#262180"/><circle cx="18" cy="18" r="3.5" fill="#fff"/><circle cx="27" cy="18" r="3.5" fill="#fff"/><circle cx="36" cy="18" r="3.5" fill="#fff"/></svg>SMS</div>
<div class="abs service" style="left:358px;width:225px">
  <svg width="44" height="36" viewBox="0 0 44 36"><rect x="2" y="10" width="40" height="24" fill="none" stroke="#262180" stroke-width="2.5"/><path d="M2 10l20 14 20-14M22 2 2 10M22 2l20 8" fill="none" stroke="#262180" stroke-width="2.5"/></svg>EMAIL</div>
<div class="abs service service-active" style="left:615px;width:225px"><span class="sq"></span>SOCIAL AD</div>
<div class="service-note abs">Newsfeed ads to people in your open house area</div>
<div class="abs service" style="left:875px;width:225px">
  <svg width="58" height="46" viewBox="0 0 58 46"><ellipse cx="24" cy="18" rx="20" ry="14" fill="none" stroke="#262180" stroke-width="4"/><path d="M12 30l-6 12 14-9" fill="#262180"/><path d="M40 12a16 12 0 0 1 4 26l6 6-12-3" fill="none" stroke="#262180" stroke-width="4"/></svg>VB</div>

<footer class="abs site-footer"></footer>
<div class="abs footer-brand" style="color:#fff"><span class="sq"></span><span class="name">Tally Porch Helpers</span></div>
<p class="abs footer-head" style="left:466px;color:#fff">FOLLOW US ON</p>
<div class="abs socials"><span></span><span></span><span class="on"></span><span></span></div>
<p class="abs footer-head" style="left:800px;color:#fff">NEWSLETTER SUBSCRIBE</p>
<div class="abs email-field" style="color:#fff">Enter Email
  <svg width="16" height="12" viewBox="0 0 16 12"><rect width="16" height="12" fill="#fff"/><path d="M0 0l8 6 8-6" fill="none" stroke="#262180" stroke-width="1.5"/></svg></div>
<div class="abs subscribe" style="color:#fff">SUBSCRIBE</div>
<div class="abs footer-rule"></div>
<p class="abs copyright" style="color:#fff">Copyrights © 2018 Tally Porch Helpers.&nbsp; All Rights Reserved.</p>

</body>
</html>
```